Plakat-Design für Immobilienmakler und Baufinanzierer
Zielgruppe
Wir sind Immobilienmakler und Baufinanzierer und suchen ein hochwertiges Design, unsere Zielgruppe sind Kunden, die Ihr Haus verkaufen möchten. Für jeden erfolgreichen Verkauf spenden wir 5 % unserer Maklercourtage an einen Verein, den sich der Kunde aussuchen darf. Mit diesem Plakat wollen wir auf unsere Vereinsförderng aufmerksam machen und Vereine ansprechen.
Aufgabenstellung
Text: 'Wir spenden 5 % unserer Provision für Ihren Verein', 'Nur 1,99 % Maklercourtage', Logo, Kontaktdaten

```html
<!DOCTYPE html>
<html lang="de">
<head>
<meta charset="utf-8">
<title>Brandel Immobilien – Vereinsförderung</title>
<link href="https://fonts.googleapis.com/css2?family=Raleway:wght@300;400;600;700;800&family=Cinzel:wght@500&display=swap" rel="stylesheet">
<style>
  :root {
    --page-bg: #e9e9e6;
    --paper: #f3f2ee;
    --teal: #1d5f68;
    --teal-deep: #164c54;
    --teal-light: #2a7077;
    --ink-light: #f1f1ec;
    --accent: #8cc8c6;
    --brand: #1f5e66;
  }
  * { box-sizing: border-box; margin: 0; padding: 0; }
  html, body { width: 1200px; height: 1200px; overflow: hidden; }
  body {
    background: var(--page-bg);
    font-family: "Raleway", sans-serif;
    position: relative;
  }
  .poster {
    position: absolute;
    left: 207px; top: 50px;
    width: 786px; height: 1100px;
    background: var(--teal);
    box-shadow: 0 6px 24px rgba(0,0,0,.18);
    overflow: hidden;
  }
  .poster__header {
    position: absolute; left: 0; top: 0;
    width: 100%; height: 176px;
    background: var(--paper);
    display: flex; align-items: center; justify-content: center;
    gap: 14px;
  }
  .brand-mark {
    width: 18px; height: 18px;
    background: var(--brand);
  }
  .brand-name {
    font-family: "Raleway", sans-serif;
    font-weight: 600;
    font-size: 26px;
    letter-spacing: 3px;
    color: var(--brand);
    text-transform: uppercase;
  }
  .poster__visual {
    position: absolute; left: 0; top: 176px;
    width: 100%; height: 924px;
    background:
      radial-gradient(ellipse at 85% 40%, rgba(40,110,80,.45), transparent 55%),
      radial-gradient(ellipse at 30% 70%, rgba(60,120,125,.35), transparent 60%),
      linear-gradient(170deg, var(--teal-light) 0%, var(--teal) 45%, var(--teal-deep) 100%);
  }
  .headline {
    position: absolute; left: 0; top: 268px;
    width: 100%;
    text-align: center;
    color: var(--ink-light);
    text-transform: uppercase;
    line-height: 63px;
    font-size: 60px;
  }
  .headline__strong { font-weight: 800; display: block; }
  .headline__light { font-weight: 300; display: block; }
  .divider {
    position: absolute; left: 188px; top: 544px;
    width: 413px; height: 3px;
    background: var(--accent);
  }
  .fee-note {
    position: absolute; left: 0; top: 558px; width: 100%;
    text-align: center;
    font-weight: 700; font-size: 21px;
    color: var(--accent);
    text-transform: uppercase;
  }
  .footer {
    position: absolute; left: 68px; right: 68px; top: 990px;
    color: var(--ink-light);
  }
  .footer__title {
    display: flex; align-items: center; gap: 14px;
    font-weight: 700; font-size: 15px;
  }
  .footer__rule { flex: 1; height: 2px; background: var(--ink-light); }
  .footer__contacts {
    display: flex; justify-content: space-between;
    margin-top: 22px;
    font-size: 13px; line-height: 17px; font-weight: 400;
  }
  .footer__contacts .col--right { text-align: right; }
</style>
</head>
<body>
  <main class="poster">
    <header class="poster__header">
      <span class="brand-mark"></span>
      <span class="brand-name">Brandel Immobilien</span>
    </header>

    <div class="poster__visual" role="img" aria-label="Getönte Fotografie einer efeubewachsenen Altbaufassade"></div>

    <h1 class="headline">
      <span class="headline__strong">Wir spenden 5 %</span>
      <span class="headline__light">unserer Provision</span>
      <span class="headline__strong">für Ihren Verein</span>
    </h1>

    <div class="divider"></div>
    <p class="fee-note">Nur 1,99 % Maklercourtage</p>

    <footer class="footer">
      <div class="footer__title">
        <span>Brandel Immobilien</span>
        <span class="footer__rule"></span>
      </div>
      <div class="footer__contacts">
        <div class="col">Lindenweg 7<br>41063 Mörsfeld</div>
        <div class="col">Tel: 02161 382 17 60<br>Mobil: 0171 624 508 93</div>
        <div class="col col--right">info@brandel-immobilien.de<br>www.brandel-immobilien.de</div>
      </div>
    </footer>
  </main>
</body>
</html>
```